Bonusheft für Patienten als kleine DIN A6 Broschüre
Zielgruppe
Bonusheft für Patienten als kleine DIN A6 Broschüre in der Zahn-Prophylaxe. Die Texte haben wir bereits vollständig formuliert, auch die Gliederung ist vorgegeben.
Wir sind eine Zahnarztpraxis mit dem Schwerpunkt Prophylaxe. Für unsere Prophylaxeabteilung möchten wir eine DIN A6 Broschüre entwerfen lassen, die als Bonusheft für Patienten dient.
Inhalt: Informationen über unsere Praxis, die leitende Mitarbeiterin, individuelle Risiken und Empfehlungen der Patienten. Auch Fakten und Tipps zur Verbesserung der Mundhygiene und Putzgewohnheiten werden Beschrieben.
Aufgabenstellung
Broschüre als DIN A6 Bonusheft mit circa sieben gestalteten Seiten, bei denen wir den Aufbau und die exakten Texte bereits vollständig vorgeben. Zusätzlich folgen mehrere gleiche Seiten, bei denen die Termine und Stempel eingetragen werden (ca. fünf Seiten).
Für Ihre Orientierung haben wir unsere Fotos und Farbschema von vorhandenen Designs unserer Praxis bereitgestellt.
Orientieren Sie sich gerne an unserer vorhandenen Homepage im Hinblick auf unseren Stil und das Praxislogo.
Homepage: www.zahnpflege-am-lindenbogen.de
Wir stellen einige Fotos zur Verwendung bereit. Falls nötig, verwenden Sie auch Stock Fotos.
Im folgenden werden wir den gewünschten Aufbau mit den Texten je Seite detailliert vorstellen. Ihre Aufgabe ist es, dies in ein modernes, frisches, ansprechendes und kompetentes Design umzusetzen.
1. Seite / Cover
- Mit Praxislogo
- Text: „Mein Prophylaxepass“
2. Seite:
- Überschrift: „Sie lassen nicht jeden an Ihre Zähne? Wir auch nicht.“
-Text: „Herzlich Willkommen! Mein Name ist Wiebke und ich arbeite als leitende Mitarbeiterin im Prophylaxe Zentrum Talbrück. Momentan befinde ich mich in der Weiterbildung zur Dentalhygienikerin und bin begeistert von der Arbeit in der präventiven Zahnmedizin. Mit meinem Wissen und meiner Erfahrung möchte ich dazu beitragen, dass unsere Patienten sich bei uns wohl und gut betreut fühlen. Ich freue mich darauf, Ihnen zu helfen, Ihre Zahngesundheit zu erhalten und zu verbessern!“
- Foto einer Mitarbeiterin
4. Seite:
- Überschrift: „Die professionelle Zahnreinigung – Wellness & Prävention“
- Text: „Eine wichtige Präventionsmaßnahme ist die regelmäßige Zahnreinigung in unserem Prophylaxe-Zentrum. Karies, Mundgeruch und Zahnfleischerkrankungen werden effektiv vorgebeugt. Die Zahnreinigung ist ein Teil der individuell geplanten Prophylaxe und eine sinnvolle Ergänzung der häus..

```html
<!DOCTYPE html>
<html lang="de">
<head>
<meta charset="utf-8">
<title>Mein Prophylaxepass – Broschüre</title>
<link href="https://fonts.googleapis.com/css2?family=Questrial&family=Montserrat:wght@400;600&display=swap" rel="stylesheet">
<style>
:root{
  --stage:#e4e4e4;
  --paper:#ffffff;
  --sand:#ebe9e1;
  --sand-dark:#d9d4c2;
  --accent:#c9c19b;
  --accent-soft:#ddd7bd;
  --ink:#1d1d1b;
  --muted:#6b6b66;
  --line:#d6d3c8;
  --form-bg:#f7f8f9;
}
*{box-sizing:border-box;margin:0;padding:0}
html,body{width:1200px;height:4471px;overflow:hidden}
body{background:var(--stage);font-family:"Questrial",sans-serif;color:var(--ink);
  display:flex;flex-direction:column;align-items:center;justify-content:space-evenly}
.spread{position:relative;width:1060px;height:740px;box-shadow:0 6px 18px rgba(0,0,0,.12)}
.page{position:absolute;top:0;width:530px;height:740px;background:var(--paper);border-top:10px solid var(--accent-soft);overflow:hidden}
.page.left{left:0}
.page.right{left:530px;border-left:1px solid #d0d0d0}
.page.sand{background:var(--sand)}
.folio{position:absolute;bottom:18px;font-size:10px;color:var(--muted)}
.left .folio{left:40px}
.right .folio{right:40px}
.folio .dot{display:inline-block;width:6px;height:6px;border-radius:50%;background:var(--accent);margin-left:6px;vertical-align:middle}
.brand{font-family:"Questrial",sans-serif;color:var(--ink);font-size:22px;line-height:1.05}
.brand .mark{display:inline-block;width:18px;height:18px;background:var(--accent);margin-bottom:6px}
.brand small{display:block;font-size:9px;color:var(--ink);margin-top:6px}
.photo{position:absolute;background:linear-gradient(135deg,#b9c6cf,#e8dccb 55%,#f4f1ec)}
h2{font-weight:400;font-size:34px;line-height:1.15}
h2 .accent{color:var(--accent)}
.body{font-size:12px;line-height:1.75}

.stamp-head{position:absolute;top:0;left:0;right:0;height:210px;background:var(--sand)}
.stamp-head .bar{position:absolute;bottom:0;width:210px;height:10px;background:var(--sand-dark)}
.left .stamp-head .bar{right:0}
.right .stamp-head .bar{left:0}
.stamp-head .brand{position:absolute;top:50px}
.left .stamp-head .brand{left:40px}
.right .stamp-head .brand{right:40px;text-align:right}
.handover{position:absolute;top:70px;font-size:11px;width:200px}
.left .handover{left:280px}
.right .handover{left:40px}
.handover p{margin-bottom:40px}
.stamp-body{position:absolute;top:210px;left:0;right:0;bottom:0;background:var(--form-bg)}
.appt{position:absolute;left:40px;right:40px}
.appt h3{font-weight:400;font-size:19px;color:var(--accent);margin-bottom:14px}
.appt .lbl{font-family:"Montserrat",sans-serif;font-weight:600;font-size:12px;margin-bottom:12px}
.opts{display:grid;grid-template-columns:145px 145px;row-gap:14px;font-size:10px;margin-bottom:16px;margin-left:2px}
.box{display:inline-block;width:9px;height:9px;border:1px solid #aaa;margin-right:8px;vertical-align:-1px}
.when{position:absolute;top:48px;left:310px;width:140px;font-size:10px}
.when div{border-bottom:1px solid var(--line);padding-bottom:5px;margin-bottom:14px}
.when .by{margin-top:42px}
.when .ic{display:inline-block;width:9px;height:9px;background:var(--accent);margin-right:6px;vertical-align:-1px}

.big{position:absolute;top:55px;left:40px;font-size:64px;line-height:.95;color:var(--accent-soft)}
.check{position:absolute;left:40px;right:40px;top:230px;list-style:none}
.check li{height:40px;margin-bottom:10px;border:1px solid #dedbd0;border-radius:4px;background:#f3f2ec;padding:0 14px;font-size:13px;display:flex;align-items:center;justify-content:space-between}
.check li::after{content:"";width:10px;height:10px;border:1px solid #c6c3b8;border-radius:2px;background:#fff}

.tech{position:absolute;top:440px;left:70px;width:390px}
.tech .device{float:left;width:80px;height:90px;margin:0 20px 6px 0;border-radius:6px;background:linear-gradient(180deg,#e8eef2,#bfcad2)}
.tech .product{color:var(--accent)}
</style>
</head>
<body>

<section class="spread">
  <div class="page left">
    <div class="stamp-head">
      <div class="brand"><span class="mark"></span><br>Zahnpflege<br>am Lindenbogen<small>Dr. Jonas &amp; Lena Brandt mit Team</small></div>
      <div class="handover"><p>Prophylaxe Pass überreicht am:</p><p>Mitarbeiterin:</p></div>
      <div class="bar"></div>
    </div>
    <div class="stamp-body">
      <div class="appt" style="top:40px">
        <h3>Heutiger Termin</h3>
        <div class="lbl">Intervall</div>
        <div class="opts"><span><i class="box"></i>3 Monate</span><span><i class="box"></i>6 Monate</span><span><i class="box"></i>4 Monate</span><span><i class="box"></i>12 Monate</span></div>
        <div class="lbl">Terminart</div>
        <div class="opts"><span><i class="box"></i>Regulärer Termin</span><span><i class="box"></i>Kompakttermin</span></div>
        <div class="when"><div><i class="ic"></i>Datum:</div><div><i class="ic"></i>Uhrzeit:</div><div class="by">Behandelt von:</div></div>
      </div>
      <div class="appt" style="top:278px">
        <h3>Ihr nächster Termin</h3>
        <div class="lbl">Intervall</div>
        <div class="opts"><span><i class="box"></i>3 Monate</span><span><i class="box"></i>6 Monate</span><span><i class="box"></i>4 Monate</span><span><i class="box"></i>12 Monate</span></div>
        <div class="lbl">Terminart</div>
        <div class="opts"><span><i class="box"></i>Regulärer Termin</span><span><i class="box"></i>Kompakttermin</span></div>
        <div class="when"><div><i class="ic"></i>Datum:</div><div><i class="ic"></i>Uhrzeit:</div><div class="by">Behandelt von:</div></div>
      </div>
    </div>
    <div class="folio"><span class="dot"></span> | zahnpflege-am-lindenbogen.de</div>
  </div>
  <div class="page right sand">
    <h1 style="position:absolute;top:60px;left:40px;font-weight:400;font-size:44px;line-height:1.05">Mein<br>Prophylaxepass</h1>
    <div class="photo" role="img" aria-label="Foto: lächelnde Patientin im Behandlungsstuhl, daneben eine Zahnfarbskala" style="top:200px;left:110px;width:380px;height:250px;border-radius:28px"></div>
    <div class="brand" style="position:absolute;left:40px;top:560px"><span class="mark"></span><br>Zahnpflege<br>am Lindenbogen<small>Dr. Jonas &amp; Lena Brandt mit Team</small></div>
    <div style="position:absolute;right:40px;top:575px;font-size:9px;line-height:1.6;color:var(--muted)">Lindenallee 12<br>40000 Talbrück<br>Tel. 0000 123456<br>Fax 0000 123457<br>info@lindenbogen.de</div>
  </div>
</section>

<section class="spread">
  <div class="page left">
    <h2 style="position:absolute;top:120px;left:60px">Sie lassen nicht jeden<br>an Ihre Zähne?<br><span class="accent">Wir auch nicht.</span></h2>
    <div style="position:absolute;top:300px;left:60px;width:50px;height:3px;background:var(--accent)"></div>
    <p class="body" style="position:absolute;top:340px;left:60px;width:380px;font-size:11.5px"><strong style="font-family:Montserrat,sans-serif;font-weight:600">Herzlich Willkommen!</strong><br>Mein Name ist Wiebke und ich arbeite als leitende Mitarbeiterin im Prophylaxe Zentrum Talbrück. Momentan befinde ich mich in der Weiterbildung zur Dentalhygienikerin und bin begeistert von der Arbeit in der präventiven Zahnmedizin. Mit meinem Wissen und meiner Erfahrung möchte ich dazu beitragen, dass unsere Patienten sich bei uns wohl und gut betreut fühlen. Ich freue mich darauf, Ihnen zu helfen, Ihre Zahngesundheit zu erhalten und zu verbessern!</p>
    <div class="folio">2</div>
  </div>
  <div class="page right">
    <div style="position:absolute;top:100px;left:60px;width:440px;height:560px;border-radius:40px;background:var(--sand)"></div>
    <div class="photo" role="img" aria-label="Foto: Mitarbeiterin in grüner Praxiskleidung mit Zahnmodell" style="top:60px;left:100px;width:400px;height:600px;border-radius:40px 0 40px 0;background:linear-gradient(180deg,#f2f2f0,#d9d4c6 40%,#5f8574)"></div>
    <div class="folio">zahnpflege-am-lindenbogen.de <span class="dot"></span></div>
  </div>
</section>

<section class="spread">
  <div class="page left">
    <h2 style="position:absolute;top:290px;left:80px">Die professionelle<br>Zahnreinigung<br><span class="accent">– Wellness &amp; Prävention</span></h2>
    <p class="body" style="position:absolute;top:440px;left:80px;width:380px">Eine wichtige Präventionsmaßnahme ist die regelmäßige Zahnreinigung in unserem Prophylaxe-Zentrum. Karies, Mundgeruch und Zahnfleischerkrankungen werden effektiv vorgebeugt. Die Zahnreinigung ist ein Teil der individuell geplanten Prophylaxe und eine sinnvolle Ergänzung der häuslichen Zahnpflege, gerade an den Stellen, wo die eigene Zahnbürste nicht hinkommt. Schonend werden alle harten und weichen Beläge von allen Zahnoberflächen entfernt — inklusive Kaffee-, Tee- und Raucherbelägen.</p>
    <div class="folio">4</div>
  </div>
  <div class="page right">
    <p class="body" style="position:absolute;top:55px;left:180px;width:290px">Natürlich weiße Zähne ! Nach der professionellen Zahnreinigung stellt sich Ihre natürliche Zahnfarbe wieder ein und ein frisches Mundgefühl entsteht. In den meisten Fällen werden die Zähne nach der Prophylaxe heller. Erhöhen Sie Ihre Lebensqualität!</p>
    <h2 style="position:absolute;top:290px;left:70px">Moderne Technik<br>für eine bessere<br><span class="accent">Behandlung</span></h2>
    <div class="tech">
      <div class="device" role="img" aria-label="Produktfoto: Gerät für die Zahnreinigung"></div>
      <p class="body">Für unsere Prophylaxebehandlungen nutzen wir aktuelle Behandlungsmethoden und bedienen uns neuer Technologie wie dem <span class="product">Glanzstrahl Pro</span>. Dadurch gewährleisten wir für unsere Patienten eine leise und angenehme Behandlung. Gleichzeitig stellen wir eine ausgezeichnete Behandlungsqualität sicher, welche Ihre Zähne nachhaltig schützt und Krankheiten vorbeugt</p>
    </div>
    <div class="folio">zahnpflege-am-lindenbogen.de | <span class="dot"></span></div>
  </div>
  <div class="photo" role="img" aria-label="Foto: zwei lächelnde junge Frauen in heller Praxisumgebung" style="top:10px;left:0;width:670px;height:225px;border-radius:0 0 30px 0;background:linear-gradient(90deg,#d9c9b0,#e9eef2 45%,#dcd0bc)"></div>
</section>

<section class="spread">
  <div class="page left sand">
    <div class="big">Risikoanalyse</div>
    <ul class="check">
      <li>Kariesaktivität</li><li>Empfindliches Zahnfleisch</li><li>Erosionen / Säureschäden</li><li>Zahnschmelzverlust</li><li>Weicher Zahnschmelz</li><li>Halitosis (Mundgeruch)</li><li>Zahnverfärbungen</li><li>Rauchen</li><li>Retainer</li>
    </ul>
    <div class="folio">6</div>
  </div>
  <div class="page right sand">
    <div class="big">Ergänzende<br>Pflegetipps</div>
    <ul class="check">
      <li>Zahnseide</li><li>Superfloss</li><li>Zahnseidesticks</li><li>Interdentalbürstchen</li><li>Zungenreinigung</li><li>Intensiv Fluoridierung</li><li>1x wöchentliche Spezial Zahnpasta</li><li>Munddusche</li><li>Mundspüllösung</li>
    </ul>
    <div class="folio">zahnpflege-am-lindenbogen.de | <span class="dot"></span></div>
  </div>
</section>

<section class="spread">
  <div class="page left">
    <div class="stamp-head">
      <div class="brand"><span class="mark"></span><br>Zahnpflege<br>am Lindenbogen<small>Dr. Jonas &amp; Lena Brandt mit Team</small></div>
      <div class="handover"><p>Prophylaxe Pass überreicht am:</p><p>Mitarbeiterin:</p></div>
      <div class="bar"></div>
    </div>
    <div class="stamp-body">
      <div class="appt" style="top:40px">
        <h3>Heutiger Termin</h3>
        <div class="lbl">Intervall</div>
        <div class="opts"><span><i class="box"></i>3 Monate</span><span><i class="box"></i>6 Monate</span><span><i class="box"></i>4 Monate</span><span><i class="box"></i>12 Monate</span></div>
        <div class="lbl">Terminart</div>
        <div class="opts"><span><i class="box"></i>Regulärer Termin</span><span><i class="box"></i>Kompakttermin</span></div>
        <div class="when"><div><i class="ic"></i>Datum:</div><div><i class="ic"></i>Uhrzeit:</div><div class="by">Behandelt von:</div></div>
      </div>
      <div class="appt" style="top:278px">
        <h3>Ihr nächster Termin</h3>
        <div class="lbl">Intervall</div>
        <div class="opts"><span><i class="box"></i>3 Monate</span><span><i class="box"></i>6 Monate</span><span><i class="box"></i>4 Monate</span><span><i class="box"></i>12 Monate</span></div>
        <div class="lbl">Terminart</div>
        <div class="opts"><span><i class="box"></i>Regulärer Termin</span><span><i class="box"></i>Kompakttermin</span></div>
        <div class="when"><div><i class="ic"></i>Datum:</div><div><i class="ic"></i>Uhrzeit:</div><div class="by">Behandelt von:</div></div>
      </div>
    </div>
    <div class="folio"><span class="dot"></span> | zahnpflege-am-lindenbogen.de</div>
  </div>
  <div class="page right">
    <div class="stamp-head">
      <div class="brand"><span class="mark"></span><br>Zahnpflege<br>am Lindenbogen<small>Dr. Jonas &amp; Lena Brandt mit Team</small></div>
      <div class="handover"><p>Prophylaxe Pass überreicht am:</p><p>Mitarbeiterin:</p></div>
      <div class="bar"></div>
    </div>
    <div class="stamp-body">
      <div class="appt" style="top:40px">
        <h3>Heutiger Termin</h3>
        <div class="lbl">Intervall</div>
        <div class="opts"><span><i class="box"></i>3 Monate</span><span><i class="box"></i>6 Monate</span><span><i class="box"></i>4 Monate</span><span><i class="box"></i>12 Monate</span></div>
        <div class="lbl">Terminart</div>
        <div class="opts"><span><i class="box"></i>Regulärer Termin</span><span><i class="box"></i>Kompakttermin</span></div>
        <div class="when"><div><i class="ic"></i>Datum:</div><div><i class="ic"></i>Uhrzeit:</div><div class="by">Behandelt von:</div></div>
      </div>
      <div class="appt" style="top:278px">
        <h3>Ihr nächster Termin</h3>
        <div class="lbl">Intervall</div>
        <div class="opts"><span><i class="box"></i>3 Monate</span><span><i class="box"></i>6 Monate</span><span><i class="box"></i>4 Monate</span><span><i class="box"></i>12 Monate</span></div>
        <div class="lbl">Terminart</div>
        <div class="opts"><span><i class="box"></i>Regulärer Termin</span><span><i class="box"></i>Kompakttermin</span></div>
        <div class="when"><div><i class="ic"></i>Datum:</div><div><i class="ic"></i>Uhrzeit:</div><div class="by">Behandelt von:</div></div>
      </div>
    </div>
    <div class="folio">zahnpflege-am-lindenbogen.de | <span class="dot"></span></div>
  </div>
</section>

</body>
</html>
```